Gaming company needs web presence

PLEASE NOTE: We need just a simple web site. We are at least a year away from launching our first product, so the site only needs a small amount of information on it. The only people who will be visiting the web site are prospective employees, prospective investors who want a little information on the company, journalists who want a little more information, and people in the games industry who will visit to read blog posts about the development of our first game.

Lanternfield Games is a new gaming company that wants to change how people think about video games. We are making games that we think can be so interesting to watch that people might want to tune into them instead of the TV.

The games we make are sophisticated, they are not for children, and we want to project an image of being serious about our craft and the brand we're trying to create. Our games are heavily focused on players interacting with each other in sophisticated ways: to negotiate, to compete, to fight, to come to each other's rescue, to cheer each other on, or to simply watch each other in awe.

We do not want a site that features lots of video game cliches like joysticks, 8 bit graphics, science fiction themes, or military themes. We are focused on craftsmanship, so we'd like to project a sense of precision, pride and deep purpose.

The purpose of this website is to create an image of our company that can help us recruit like-minded craftspeople and help find business partners. There will be no e-commerce, account creation, or forums for some time. The site should have:
-A front page that describes our business
-A section that describes our first game (we have only one for now)
-A section for employees to write blog posts. There should be something on the home page that shows links to the latest 3 blog posts.
-A section about founders that shows information about them.
-Contact information, lets people send us email

Our first game is one that looks very realistic. It takes place on a tropical island. We can't say a lot more about it in public yet, but I will say these things: it is not a game that children will play, it is not very violent, it would look more like a film than a typical video game.

And the site should be easily extendable when we have more content and more categories of content.

I've attached our official company logo with a color scheme we've been using, plus an alternate version of the logo. Please use this as a starting point for the web site's visual design. Also, I do not think it is necessary to use the dark background in the logo as the background throughout the site. I wouldn't rule it out, but I'd like to see some proposals with lighter backgrounds.

We need to be able to get code from you so that we can drop it on our server and get it running without extra effort. We need to be able to add content for Blog posts easily as well, so please indicate how that would work.
Updates

Hello everyone, Thanks for all of the great submissions so far. There are some important things I'd like to relay to everyone: We are at least a year away from launching our first game, so we only need a simple web site. Unfortunately, we can't share any screenshots or details about our first game yet. All of these submissions look great, but are far too complicated. Also, I really want to stress that we don't want to feature stock photography of people playing games, especially of children playing games. In fact, since we don't want to release any screenshots of our games and we don't have any good photography of ourselves working, it's best if there are no photographic images on the site for now.

Hello designers, Can you let me know if your designs include all the code that would let us drop the files on to our web server and easily get it up and running? Also, can you tell me how the blog posts would be created? Does your code run on a CMS? Thanks, Haskell

Hi Designers, we will be hosting this site with Wordpress, so we would prefer to have submissions ready to go on a Wordpress server. Thanks!

Target Market(s)

Investors, prospective employees, press, blog post readers.

Industry/Entity Type

Business

Font styles to use
Sans Serif

Requirements
Must have
• Simplicity first. Please use a color palette and fonts that match our logo.
Should not have
• Video game cliches. Flash animations or menus.
No children.
No photographs of people playing games.

(I realize this is very limiting, but we're keeping the sits as simple as possible for now)

```html
<!DOCTYPE html>
<html lang="en">
<head>
<meta charset="utf-8">
<title>Lanternfield Games</title>
<link rel="stylesheet" href="https://fonts.googleapis.com/css2?family=Stardos+Stencil:wght@400;700&family=Noto+Serif:ital,wght@0,400;1,400&display=swap">
<style>
:root{
  --wood-dark:#2b190f;
  --wood:#3e2617;
  --wood-light:#4a2d1b;
  --orange:#d0803e;
  --orange-deep:#b96a2c;
  --cream:#f5efe6;
  --white:#ffffff;
  --ink:#3a2012;
  --muted:#8a7a6c;
  --panel:rgba(20,10,5,.35);
  --footer:#1c0f08;
}
*{margin:0;padding:0;box-sizing:border-box}
html,body{width:672px;height:1200px;overflow:hidden}
body{
  position:relative;
  background:linear-gradient(90deg,var(--wood-dark),var(--wood) 30%,var(--wood-light) 55%,var(--wood) 80%,var(--wood-dark));
  font-family:"Noto Serif",Georgia,serif;
  color:var(--white);
}
.abs{position:absolute}
.stencil{font-family:"Stardos Stencil",Georgia,serif;font-weight:700;text-transform:uppercase}
.brand{left:74px;top:24px;width:170px}
.brand-name{font-family:"Stardos Stencil",serif;font-weight:700;font-size:24px;line-height:24px;color:var(--white);letter-spacing:1px}
.brand-sub{font-family:"Stardos Stencil",serif;font-weight:700;font-size:14px;line-height:20px;color:var(--white);letter-spacing:4px;text-align:center;border-top:2px solid var(--orange);border-bottom:2px solid var(--orange);margin-top:4px;width:160px}
.search{left:420px;top:32px;width:178px;height:26px;border:1px solid #cbbfb3;background:rgba(255,255,255,.12);font-size:7px;color:#eee;font-family:Arial,sans-serif;padding:8px 6px}
.search svg{position:absolute;right:7px;top:7px}
.nav{left:74px;top:86px;width:524px;height:36px;background:var(--orange);border-bottom:2px solid var(--orange-deep);display:flex;justify-content:space-around;align-items:center;padding:0 8px}
.nav a{color:var(--white);text-decoration:none;font-size:10.5px;letter-spacing:.5px}
.hero{left:74px;top:123px;width:524px;height:263px;background:linear-gradient(135deg,#e9e4dc,#c9b9a8 45%,#6a5fa0 85%,#ddd)}
.dots{left:100px;top:373px;display:flex;gap:3px}
.dots span{width:8px;height:8px;border-radius:50%;border:1.5px solid var(--orange)}
.dots span.on{border-color:#222}
h2{font-size:14px;color:var(--white);letter-spacing:.5px}
h2 .lead{color:var(--orange);font-size:21px}
.welcome{left:74px;top:400px;width:324px}
.welcome p,.founder p,.game p{font-style:italic;font-size:6.4px;line-height:14px;color:var(--cream)}
.welcome p{margin-top:10px}
.dash{height:0;border-top:3px dashed var(--orange)}
.founder-photo{left:76px;top:568px;width:112px;height:100px;background:var(--white);padding:7px}
.founder-photo div{width:100%;height:100%;background:linear-gradient(135deg,#d8d6d2,#9c8b7b)}
.founder-text{left:200px;top:568px;width:198px}
.founder-text h3{font-size:11px;color:var(--orange);margin-bottom:6px}
.founder-text p{font-style:italic;font-size:6.4px;line-height:14px;color:var(--cream)}
.blog{left:408px;top:432px;width:188px;height:212px;background:var(--white);padding:16px 10px 0 12px}
.post{display:flex;gap:10px;margin-bottom:22px}
.date{width:30px;text-align:center;color:var(--ink)}
.date b{display:block;font-family:"Stardos Stencil",serif;font-size:17px;line-height:16px}
.date small{font-family:"Stardos Stencil",serif;font-weight:700;font-size:8.5px}
.post h4{font-size:9.5px;color:var(--orange);margin-bottom:3px}
.post p{font-style:italic;font-size:5.5px;line-height:9px;color:var(--muted)}
.arrows{left:565px;top:709px;display:flex;gap:5px}
.arrows span{width:14px;height:14px;border-radius:50%;display:flex;align-items:center;justify-content:center}
.games{left:74px;top:730px;width:524px;display:flex;gap:9px}
.game{width:124px}
.game .thumb{width:124px;height:85px;border:2px solid var(--white)}
.game h3{font-size:8px;margin:10px 0 8px;letter-spacing:.3px}
.rule{left:74px;top:920px;width:524px;border-top:1px solid #cbbfb3}
.btn{border:1px solid #cbbfb3;background:#5a4438;color:var(--cream);font-style:italic;font-size:11px;text-align:center}
.more{left:274px;top:909px;width:124px;height:24px;line-height:22px}
.contact{left:74px;top:946px;width:524px;height:208px;background:var(--panel)}
.field{border:1px solid #e8e0d8;font-size:7.5px;padding:6px 7px;color:var(--white);letter-spacing:.5px}
.subscribe{left:284px;top:1115px;width:104px;height:24px;line-height:22px}
.footer{left:0;top:1154px;width:672px;height:46px;background:var(--footer)}
.copy{left:74px;top:1174px;font-family:Arial,sans-serif;font-size:6.5px;color:#ddd}
.social{left:488px;top:1167px;display:flex;gap:6px}
.social span{width:18px;height:18px;border:1.5px solid #eee;border-radius:50%}
.tag{left:611px;top:1186px;font-family:Arial,sans-serif;font-size:6px;color:#ddd}
</style>
</head>
<body>
<header>
  <div class="abs brand">
    <div class="brand-name">LANTERNFIELD</div>
    <div class="brand-sub">GAMES</div>
  </div>
  <div class="abs search">Enter Any Keyword.....
    <svg width="10" height="10" viewBox="0 0 10 10"><circle cx="6" cy="4" r="3" fill="none" stroke="#fff" stroke-width="1.3"/><line x1="4" y1="6" x2="1" y2="9" stroke="#fff" stroke-width="1.6"/></svg>
  </div>
  <nav class="abs nav stencil">
    <a href="#">Home</a><a href="#">About Us</a><a href="#">Blog</a><a href="#">Founders</a><a href="#">Our Games</a><a href="#">News</a><a href="#">Contact Us</a>
  </nav>
  <div class="abs hero" role="img" aria-label="Banner photo of a group of friends on a sofa in a bright living room"></div>
  <div class="abs dots"><span></span><span></span><span class="on"></span></div>
</header>

<section class="abs welcome">
  <h2 class="stencil"><span class="lead">Welcome</span>&nbsp; <span style="font-size:10px">to Lanternfield Games</span></h2>
  <p>Lorem Ipsum is simply dummy text of the printing and typesetting industry. Lorem Ipsum has been the industry's standard dummy text ever since the 1500s, when an unknown printer took a galley of type and scrambled it to make a type specimen book. It has survived not only five centuries, but also the leap into electronic typesetting, remaining essentially unchanged scrambled it to make a type specimen book. It has survived not only five centuries, but also the leap into electronic typesetting......</p>
</section>
<div class="abs dash" style="left:74px;top:521px;width:324px"></div>

<h2 class="abs stencil" style="left:74px;top:536px"><span class="lead" style="font-size:17px">About</span> our founders</h2>
<div class="abs founder-photo" role="img" aria-label="Portrait of a founder"><div></div></div>
<div class="abs founder-text">
  <h3 class="stencil">Neque porro quisquam</h3>
  <p>Sed ut perspiciatis unde omnis iste natus error sit voluptatem accusantium doloremque laudantium, totam rem aperiam, eaque ipsa quae ab illo inventore veritatis et quasi architecto beatae vitae dicta sunt explicabo.Sed ut perspiciatis unde omnis iste natus error sit voluptatem accusantium doloremque laudantium, totam rem tecto beatae vitae dicta sunt explicabo.</p>
</div>

<h2 class="abs stencil" style="left:408px;top:404px"><span class="lead" style="font-size:17px">Latest</span> blog posts</h2>
<aside class="abs blog">
  <div class="post"><div class="date"><b>25</b><small>JUNE</small></div><div><h4 class="stencil">New game released!</h4><p>Lorem Ipsum is simply dummy text of the printing and typesetting industry.</p></div></div>
  <div class="post"><div class="date"><b>25</b><small>JUNE</small></div><div><h4 class="stencil">New game released!</h4><p>Lorem Ipsum is simply dummy text of the printing and typesetting industry.</p></div></div>
  <div class="post"><div class="date"><b>25</b><small>JUNE</small></div><div><h4 class="stencil">New game released!</h4><p>Lorem Ipsum is simply dummy text of the printing and typesetting industry.</p></div></div>
</aside>

<div class="abs dash" style="left:74px;top:685px;width:524px"></div>
<h2 class="abs stencil" style="left:74px;top:698px"><span class="lead" style="font-size:17px">Our</span> games</h2>
<div class="abs arrows">
  <span style="background:var(--orange)"><svg width="6" height="8"><path d="M5 1L1.5 4L5 7" stroke="#fff" stroke-width="1.5" fill="none"/></svg></span>
  <span style="background:#fff"><svg width="6" height="8"><path d="M1 1L4.5 4L1 7" stroke="#222" stroke-width="1.5" fill="none"/></svg></span>
</div>
<section class="abs games">
  <article class="game"><div class="thumb" role="img" aria-label="Game artwork: buggy on a beach" style="background:linear-gradient(180deg,#6db2d8,#c9a56a 60%,#7a5a33)"></div><h3 class="stencil">Neque porro quisquam</h3><p>Sed ut perspiciatis unde omnis iste natuserr voluptatem accusantium doloemque laud totam rem aperiam,eaque ipsa quae ab illo veriatis et quasi architecto ...</p></article>
  <article class="game"><div class="thumb" role="img" aria-label="Game artwork: red race car on a road" style="background:linear-gradient(180deg,#f2c93a,#d23a2a 55%,#333)"></div><h3 class="stencil">Neque porro quisquam</h3><p>Sed ut perspiciatis unde omnis iste natuserr voluptatem accusantium doloemque laud totam rem aperiam,eaque ipsa quae ab illo veriatis et quasi architecto ...</p></article>
  <article class="game"><div class="thumb" role="img" aria-label="Game artwork: cartoon platform level" style="background:linear-gradient(180deg,#7fc6e8,#6cae4a 55%,#b44a2a)"></div><h3 class="stencil">Neque porro quisquam</h3><p>Sed ut perspiciatis unde omnis iste natuserr voluptatem accusantium doloemque laud totam rem aperiam,eaque ipsa quae ab illo veriatis et quasi architecto ...</p></article>
  <article class="game"><div class="thumb" role="img" aria-label="Game artwork: cartoon karting race" style="background:linear-gradient(180deg,#8fd0ee,#d84a3a 60%,#c8a070)"></div><h3 class="stencil">Neque porro quisquam</h3><p>Sed ut perspiciatis unde omnis iste natuserr voluptatem accusantium doloemque laud totam rem aperiam,eaque ipsa quae ab illo veriatis et quasi architecto ...</p></article>
</section>

<div class="abs rule"></div>
<div class="abs btn more">View More Games</div>

<section class="abs contact">
  <h2 class="abs stencil" style="left:2px;top:18px"><span class="lead" style="font-size:17px">Quick</span> contact</h2>
  <div class="abs field stencil" style="left:3px;top:57px;width:163px;height:22px">Name :</div>
  <div class="abs field stencil" style="left:181px;top:57px;width:163px;height:22px">Email :</div>
  <div class="abs field stencil" style="left:358px;top:57px;width:163px;height:22px">Phone :</div>
  <div class="abs field stencil" style="left:3px;top:92px;width:518px;height:64px">Messages :</div>
</section>
<div class="abs btn subscribe">Subscribe</div>

<footer class="abs footer"></footer>
<div class="abs copy">© Copyright 2014 Lanternfield Games.All Right Reseved.</div>
<div class="abs social"><span></span><span></span><span></span><span></span><span></span></div>
<div class="abs tag">C2</div>
</body>
</html>
```